High Tech Real Estate Startup needs a business card

We are developing an innovative real estate marketing product based around advanced search and virtual reality.

We talk to people, we need business cards.

Target Market(s)

The target market is technology professionals and realtors.

Contact Information for Business Card

The information to be included will include

Name
Title
Phone Number
E-mail Address
www.zelquin.com

It should use simple iconography for each one of those fields.

Font styles to use
Other font styles liked:
• Co, Jubilat, Avenir

Colors

Designer to choose colors to be used in the design.

Requirements
Must have
• Clean aesthetic,
• Good use of negative space.
• It should use our company logo, shown in the attached file. It is able to use the negative of that logo (coloured font and white background) and I have attached other acceptable accent colours in a swatch file.
Should not have
• Should not be too busy
• No extraneous text (slogans, tag lines etc)

```html
<!DOCTYPE html>
<html lang="en">
<head>
<meta charset="utf-8">
<title>Zelquin Business Card</title>
<link rel="stylesheet" href="https://fonts.googleapis.com/css2?family=Montserrat:wght@400;500;600&display=swap">
<style>
  :root {
    --teal: #14b6b6;
    --gold: #e2c74b;
    --ink: #4f4f4f;
    --paper: #fafafa;
    --backdrop: #4a4a4a;
  }
  * { margin: 0; padding: 0; box-sizing: border-box; }
  html, body { width: 1200px; height: 1134px; overflow: hidden; }
  body {
    background: var(--backdrop);
    font-family: "Montserrat", sans-serif;
    position: relative;
  }
  .card {
    position: absolute;
    left: 261px;
    width: 675px;
  }
  .card-front { top: 161px; height: 381px; background: var(--paper); }
  .card-back  { top: 589px; height: 384px; background: var(--teal); }

  .brand-square {
    position: absolute;
    left: 150px; top: 134px;
    width: 143px; height: 142px;
    background: var(--teal);
    display: flex; align-items: center; justify-content: center;
  }
  .brand-name {
    color: #fff;
    font-weight: 500;
    letter-spacing: 0.5px;
  }
  .brand-square .brand-name { font-size: 19px; }

  .identity { position: absolute; left: 370px; top: 124px; }
  .person-name {
    color: var(--teal);
    font-size: 27px;
    font-weight: 500;
    line-height: 1;
  }
  .person-title {
    color: var(--ink);
    font-size: 19px;
    font-weight: 400;
    margin-top: 7px;
  }
  .divider {
    width: 59px; height: 2px;
    background: var(--gold);
    margin-top: 12px;
  }
  .contact-list { list-style: none; margin-top: 17px; }
  .contact-list li {
    display: flex; align-items: center;
    height: 27px;
    color: var(--ink);
    font-size: 17px;
  }
  .contact-list svg { width: 17px; height: 17px; margin-right: 9px; fill: var(--teal); }

  .card-back .brand-name {
    position: absolute;
    left: 0; right: 0; top: 50%;
    transform: translateY(-50%);
    text-align: center;
    font-size: 78px;
    letter-spacing: 2px;
  }
</style>
</head>
<body>
  <section class="card card-front">
    <div class="brand-square"><span class="brand-name">ZELQUIN</span></div>
    <div class="identity">
      <h1 class="person-name">Daniel Reyes</h1>
      <p class="person-title">President</p>
      <div class="divider"></div>
      <ul class="contact-list">
        <li>
          <svg viewBox="0 0 24 24" aria-hidden="true"><path d="M6.6 10.8c1.4 2.8 3.8 5.1 6.6 6.6l2.2-2.2c.3-.3.7-.4 1-.2 1.1.4 2.3.6 3.6.6.6 0 1 .4 1 1V20c0 .6-.4 1-1 1C10.6 21 3 13.4 3 4c0-.6.4-1 1-1h3.5c.6 0 1 .4 1 1 0 1.3.2 2.5.6 3.6.1.3 0 .7-.2 1l-2.3 2.2z"/></svg>
          987 555 0142
        </li>
        <li>
          <svg viewBox="0 0 24 24" aria-hidden="true"><path d="M2 5h20v2l-10 6L2 7z"/><path d="M2 9l10 6 10-6v10H2z"/></svg>
          info@zelquin.com
        </li>
        <li>
          <svg viewBox="0 0 24 24" aria-hidden="true"><path d="M12 2a10 10 0 100 20 10 10 0 000-20zm6.9 6h-2.9a15 15 0 00-1.4-3.6A8 8 0 0118.9 8zM12 4c.8 1.2 1.5 2.5 1.9 4h-3.8c.4-1.5 1.1-2.8 1.9-4zM4.3 14a8 8 0 010-4h3.3a16 16 0 000 4zm.8 2h2.9c.3 1.3.8 2.5 1.4 3.6A8 8 0 015.1 16zM8 8H5.1a8 8 0 014.3-3.6C8.8 5.5 8.4 6.7 8 8zm4 12c-.8-1.2-1.5-2.5-1.9-4h3.8c-.4 1.5-1.1 2.8-1.9 4zm2.3-6H9.7a14 14 0 010-4h4.6a14 14 0 010 4zm.3 5.6c.6-1.1 1.1-2.3 1.4-3.6h2.9a8 8 0 01-4.3 3.6zm1.8-5.6a16 16 0 000-4h3.3a8 8 0 010 4z"/></svg>
          www.zelquin.com
        </li>
      </ul>
    </div>
  </section>

  <section class="card card-back">
    <span class="brand-name">ZELQUIN</span>
  </section>
</body>
</html>
```